Moon Tot needs ecommerce website design help

We need someone to set up a fully functional website for us. We sell baby bibs, I attached them along with our company logo (MTG: moon tot goods). The bibs are made of 100% silicon, they are safe, light weight, soft, smooth, flexible, dishwasher safe and has funny faces.

Business name: Moon Tot Goods
Elm Hollow, NY 00000
email: MoonTotGoods@mailbox-example.com
tel.: (555) 014-TOTS
website: MoonTotGoods-example.com

Target Market(s)

18-40

Industry/Entity Type

Baby

Coding

Coded - Design and coding required

Number of Pages Required

5+ page

Requirements
Must have
• 1. Pages: Why buy from us, Contact Us, Home page, Products Page, Blog
• 2. Use the colors from our logo for the web design.
• 3. Need a link that will connect visitors to our facebook, instagram, Pinterest and Tumblr account. Would like links on,the top left side of the page
Nice to have
• My Cart page
• 1. On contact us page, we want to include some type of template for the customer to complete. (Ex: name, email address, contact number, optional home address, comments)
• 2. When clients visit our website, we want a capture/pop up for the customer to subscribe to our email list to receive discounts. (Ex. Want 10% off your next order ? Suscribe to our mailing list below and get a 10% off code to use at check out. If they don't want to subscribe, they have the option to select "No Thank You, I want to pay full price).
• 3. On home page have subscribe to our email list.

```html
<!DOCTYPE html>
<html lang="en">
<head>
<meta charset="utf-8">
<title>Moon Tot Goods</title>
<link href="https://fonts.googleapis.com/css2?family=Open+Sans:wght@400;600;700&family=Oswald:wght@400;500&display=swap" rel="stylesheet">
<style>
:root{
  --pink:#e8206f;
  --pink-dark:#c8105a;
  --green:#8cc63f;
  --green-dark:#6fa82a;
  --orange:#f7941d;
  --yellow:#f5c400;
  --blue:#29a9e0;
  --red:#e53935;
  --ink:#444;
  --muted:#888;
  --page:#f2f2f4;
  --card:#fff;
  --line:#e2e2e6;
}
*{box-sizing:border-box;margin:0;padding:0}
html,body{width:768px;height:1200px;overflow:hidden}
body{background:var(--page);font-family:"Open Sans",Arial,sans-serif;color:var(--ink);position:relative}
.abs{position:absolute}

.site-header{left:0;top:0;width:768px;height:92px;background:#fff}
.brand{left:64px;top:16px;display:flex;align-items:center;gap:8px}
.brand-dot{width:34px;height:34px;border-radius:50%;background:var(--green)}
.brand-name{font-family:"Oswald",sans-serif;font-weight:500;font-size:19px;color:var(--pink);letter-spacing:.5px}
.social-top{right:28px;top:12px;display:flex;gap:6px}
.social-top span{width:20px;height:20px;border-radius:50%;display:block}
.main-nav{left:250px;top:52px;display:flex;gap:6px}
.main-nav a{display:block;width:86px;height:38px;padding-top:10px;border-radius:6px 6px 0 0;text-align:center;color:#fff;font-size:9px;font-weight:700;text-decoration:none;letter-spacing:.3px}

.hero{left:64px;top:92px;width:640px;height:318px;background:linear-gradient(100deg,#dcc98d 0%,#e8dcae 35%,#eef0d8 60%,#d9e2b3 100%)}
.hero-copy{left:420px;top:110px;width:200px;color:#fff;font-family:"Oswald",sans-serif}
.hero-copy h1{font-size:28px;font-weight:500;line-height:1.05;text-shadow:0 1px 2px rgba(0,0,0,.25)}
.hero-copy p{font-size:14px;margin-top:6px;line-height:1.2;text-shadow:0 1px 2px rgba(0,0,0,.25)}
.btn{display:inline-block;color:#fff;font-size:8px;font-weight:700;border-radius:2px;text-align:center}
.hero-copy .btn{background:var(--pink);padding:7px 14px;margin-top:12px;font-family:"Open Sans",sans-serif}
.hero-dots{left:0;width:640px;top:290px;display:flex;justify-content:center;gap:5px}
.hero-dots i{width:8px;height:8px;border-radius:50%;background:#fff;opacity:.7}
.hero-dots i.on{background:var(--pink);opacity:1}

.newsletter{left:64px;top:422px;width:640px;height:52px;background:var(--pink);display:flex;align-items:center;padding:0 14px;gap:12px}
.newsletter svg{flex:none}
.newsletter h2{font-family:"Oswald",sans-serif;font-weight:400;color:#fff;font-size:15px;width:200px}
.newsletter .field{width:120px;height:22px;background:#fff;border-radius:2px;font-size:8px;color:#aaa;padding:5px 6px}
.newsletter .btn{background:var(--pink-dark);border:1px solid #fff;padding:6px 0;width:110px;margin-left:auto}

.side-title{background:var(--pink);color:#fff;font-size:10px;font-weight:700;padding:6px 10px;width:192px;left:64px}
.insta{left:64px;top:512px;width:192px;height:178px;background:#fff;border:1px solid var(--line);padding:8px}
.insta p{font-size:8px;color:var(--muted);line-height:1.35}
.insta-grid{display:grid;grid-template-columns:repeat(3,54px);gap:6px;margin-top:12px}
.insta-grid div{height:54px}
.promo{left:64px;top:702px;width:192px;height:100px;background:linear-gradient(135deg,#e0a77e,#c97d59);color:#fff;font-family:"Oswald",sans-serif;padding:30px 12px}
.promo span{display:block;font-size:18px;line-height:1}
.promo b{font-size:30px;font-weight:500}
.soon{left:64px;top:834px;width:192px;height:188px;background:#fff;border:1px solid var(--line);padding:10px}
.soon-item{display:flex;gap:10px;margin-bottom:18px}
.soon-item div{width:60px;height:60px;flex:none}
.soon-item h4{font-size:8px;font-weight:700;margin-top:6px}
.price{font-size:8px;color:var(--pink);font-weight:700;margin-top:4px}
.stars{color:var(--orange);font-size:8px;letter-spacing:1px}

.feat-head{left:270px;top:500px;width:434px;display:flex;align-items:center}
.feat-head h2{font-size:12px;font-weight:700;color:#555}
.arrows{margin-left:auto;display:flex;gap:3px}
.arrows span{width:14px;height:14px;background:#bbb;color:#fff;font-size:9px;text-align:center;line-height:14px}
.arrows span.on{background:var(--pink)}
.grid{left:270px;top:530px;width:434px;display:grid;grid-template-columns:repeat(3,134px);column-gap:16px;row-gap:12px}
.card{background:var(--card);border:1px solid var(--line);height:204px;padding:8px}
.card .pic{height:110px;border-radius:4px}
.card h3{font-size:8px;font-weight:700;margin-top:10px}
.card .row{display:flex;justify-content:space-between;margin-top:4px}
.card .btn{background:var(--green);padding:6px 10px;margin-top:8px}
.tag{position:relative}
.tag::after{content:"NEW";position:absolute;left:-4px;top:-4px;background:var(--green);color:#fff;font-size:6px;font-weight:700;padding:5px 4px;border-radius:50%}

.perks{left:270px;top:968px;width:434px;display:flex;gap:14px}
.perk{flex:1;background:#fff;border:1px solid var(--line);height:58px;display:flex;align-items:center;padding:0 12px;gap:10px}
.perk .ic{width:32px;height:32px;border-radius:50%;flex:none}
.perk h4{font-size:8px;font-weight:700}
.perk p{font-size:7px;color:var(--muted);line-height:1.3;margin-top:2px}

.footer{left:0;top:1036px;width:768px;height:164px}
.footer-body{left:0;top:30px;width:768px;height:104px;background:var(--pink)}
.footer-items{left:64px;top:60px;width:640px;display:flex;align-items:center;gap:26px;color:#fff;font-size:8px}
.fi{display:flex;align-items:center;gap:8px;line-height:1.4}
.fi svg{flex:none}
.fi b{display:block;font-weight:600}
.footer-social{margin-left:auto;display:flex;gap:5px}
.footer-social span{width:18px;height:18px;border-radius:50%;border:1px solid #fff;display:block}
.copyright{left:0;top:134px;width:768px;height:30px;background:var(--pink-dark);color:#fff;font-size:7px;text-align:center;line-height:30px}
</style>
</head>
<body>

<header class="site-header abs">
  <div class="brand abs"><span class="brand-dot"></span><span class="brand-name">MOON TOT GOODS</span></div>
  <div class="social-top abs">
    <span style="background:var(--green)"></span>
    <span style="background:var(--orange)"></span>
    <span style="background:var(--pink)"></span>
    <span style="background:var(--red)"></span>
  </div>
  <nav class="main-nav abs">
    <a href="#" style="background:var(--green)">HOME</a>
    <a href="#" style="background:var(--pink)">PRODUCTS</a>
    <a href="#" style="background:var(--orange)">WHY BUY FROM US</a>
    <a href="#" style="background:var(--green-dark)">BLOG</a>
    <a href="#" style="background:var(--yellow)">CONTACT US</a>
  </nav>
</header>

<section class="hero abs" role="img" aria-label="Photo of a toddler eating while wearing a pink silicon bib">
  <div class="hero-copy abs">
    <h1>SILICON BABY<br>BIBS</h1>
    <p>MADE OF 100% SILICON<br>THEY ARE SAFE</p>
    <span class="btn">SHOP NOW</span>
  </div>
  <div class="hero-dots abs"><i class="on"></i><i></i><i></i><i></i></div>
</section>

<section class="newsletter abs">
  <svg width="32" height="32" viewBox="0 0 32 32"><circle cx="16" cy="16" r="15" fill="none" stroke="#fff" stroke-width="1.5"/><rect x="8" y="11" width="16" height="11" fill="none" stroke="#fff" stroke-width="1.5"/><path d="M8 11l8 6 8-6" fill="none" stroke="#fff" stroke-width="1.5"/></svg>
  <h2>NEWSLETTER SIGN UP</h2>
  <div class="field">Enter your name</div>
  <div class="field">Enter your email</div>
  <span class="btn">SUBSCRIBE</span>
</section>

<div class="side-title abs" style="top:490px">FEATURED ON OUR INSTAGRAM</div>
<aside class="insta abs">
  <p>Share your little one's snack time with our bibs and get featured here!</p>
  <div class="insta-grid">
    <div role="img" aria-label="Baby wearing a bib" style="background:#e7c9b4"></div>
    <div role="img" aria-label="Baby wearing a bib" style="background:#d7b7a4"></div>
    <div role="img" aria-label="Baby wearing a bib" style="background:#c9d8e6"></div>
    <div role="img" aria-label="Baby wearing a bib" style="background:#cfe1b9"></div>
    <div role="img" aria-label="Baby wearing a bib" style="background:#f0d6c2"></div>
    <div role="img" aria-label="Baby wearing a bib" style="background:#d9d2e4"></div>
  </div>
</aside>
<div class="promo abs" role="img" aria-label="Promotional photo of a baby with a bib"><span>UPTO SAVE</span><b>30%</b></div>
<div class="side-title abs" style="top:812px">COMING SOON</div>
<aside class="soon abs">
  <div class="soon-item"><div role="img" aria-label="Pink bib with a funny face" style="background:#f48fb6;border-radius:6px"></div><div style="width:auto;height:auto"><h4>SLEEPY MOON BIB</h4><p class="price">$ 14.99</p><p class="stars">★★★★★</p></div></div>
  <div class="soon-item"><div role="img" aria-label="Pink bib with a funny face" style="background:#f06ca0;border-radius:6px"></div><div style="width:auto;height:auto"><h4>SLEEPY MOON BIB</h4><p class="price">$ 14.99</p><p class="stars">★★★★★</p></div></div>
</aside>

<div class="feat-head abs"><h2>FEATURES OF THE PRODUCT</h2><div class="arrows"><span>‹</span><span class="on">›</span></div></div>
<section class="grid abs">
  <article class="card"><div class="pic tag" role="img" aria-label="Pink silicon bib with a funny face" style="background:#f27aa8"></div><h3>SMILEY SILICON BIB</h3><div class="row"><span class="price">$ 14.99</span><span class="stars">★★★★★</span></div><span class="btn">SHOP NOW</span></article>
  <article class="card"><div class="pic" role="img" aria-label="Blue silicon bib with a funny face" style="background:#5bb8e8"></div><h3>SMILEY SILICON BIB</h3><div class="row"><span class="price">$ 14.99</span><span class="stars">★★★★★</span></div><span class="btn">SHOP NOW</span></article>
  <article class="card"><div class="pic" role="img" aria-label="Green silicon bib with a funny face" style="background:#9ccf5a"></div><h3>SMILEY SILICON BIB</h3><div class="row"><span class="price">$ 14.99</span><span class="stars">★★★★★</span></div><span class="btn">SHOP NOW</span></article>
  <article class="card"><div class="pic" role="img" aria-label="Orange silicon bib with a funny face" style="background:#f6a84a"></div><h3>SMILEY SILICON BIB</h3><div class="row"><span class="price">$ 14.99</span><span class="stars">★★★★★</span></div><span class="btn">SHOP NOW</span></article>
  <article class="card"><div class="pic" role="img" aria-label="Blue silicon bib with a funny face" style="background:#3fa4dc"></div><h3>SMILEY SILICON BIB</h3><div class="row"><span class="price">$ 14.99</span><span class="stars">★★★★★</span></div><span class="btn">SHOP NOW</span></article>
  <article class="card"><div class="pic" role="img" aria-label="Yellow silicon bib with a funny face" style="background:#f3d34a"></div><h3>SMILEY SILICON BIB</h3><div class="row"><span class="price">$ 14.99</span><span class="stars">★★★★★</span></div><span class="btn">SHOP NOW</span></article>
</section>

<section class="perks abs">
  <div class="perk"><span class="ic" style="background:var(--green)"></span><div><h4>DISHWASHER SAFE</h4><p>Rinse or pop it in the dishwasher, it stays like new.</p></div></div>
  <div class="perk"><span class="ic" style="background:var(--pink)"></span><div><h4>EASY TO CLEAN</h4><p>Soft silicon wipes clean in seconds after every meal.</p></div></div>
</section>

<footer class="footer abs">
  <svg class="abs" style="left:0;top:0" width="768" height="32" viewBox="0 0 768 32" preserveAspectRatio="none"><path d="M0 32 Q24 4 48 20 Q72 2 96 20 Q120 4 144 20 Q168 2 192 20 Q216 4 240 20 Q264 2 288 20 Q312 4 336 20 Q360 2 384 20 Q408 4 432 20 Q456 2 480 20 Q504 4 528 20 Q552 2 576 20 Q600 4 624 20 Q648 2 672 20 Q696 4 720 20 Q744 2 768 18 L768 32 Z" fill="#e8206f"/></svg>
  <div class="footer-body abs"></div>
  <div class="footer-items abs">
    <div class="fi"><svg width="24" height="24" viewBox="0 0 24 24"><circle cx="12" cy="12" r="11" fill="none" stroke="#fff"/><rect x="6" y="8" width="12" height="8" fill="none" stroke="#fff"/><path d="M6 8l6 5 6-5" fill="none" stroke="#fff"/></svg><div><b>Email</b>MoonTotGoods@mailbox-example.com</div></div>
    <div class="fi"><svg width="24" height="24" viewBox="0 0 24 24"><circle cx="12" cy="12" r="11" fill="none" stroke="#fff"/><path d="M12 18s-4-4.5-4-7.5a4 4 0 018 0c0 3-4 7.5-4 7.5z" fill="#fff"/><circle cx="12" cy="10.5" r="1.5" fill="#e8206f"/></svg><div><b>Address</b>Elm Hollow, NY 00000</div></div>
    <div class="fi"><svg width="24" height="24" viewBox="0 0 24 24"><circle cx="12" cy="12" r="11" fill="none" stroke="#fff"/><path d="M8.5 7l2 2-1.2 1.6a7 7 0 004 4L15 13.4l2 2-1.5 1.6C11 17 7 13 7 8.5z" fill="#fff"/></svg><div><b>Call Us</b>(555) 014-TOTS</div></div>
    <div class="footer-social"><span></span><span></span><span></span><span></span></div>
  </div>
  <div class="copyright abs">© Copyright moontotgoods 2016 All Rights Reserved</div>
</footer>

</body>
</html>
```